Maplecrest Disability - Social Security Disability Attorneys

Our company is expanding to attract clients nationwide for our social security disability practice. We have a logo, but I am looking for a creative and elegant letterhead that projects an image of being technologically advanced but still professional enough for the legal field. I am looking for the "wow factor" combined with this is still professional enough for a law practice.

Requesting letterhead and business card design
Updates

Had to update and change the logo. The previous logo had a typo. Please send updates with the new logo for consideration. The letterhead and business cards should be professional enough to be used for a law firm. Thanks.

Industry/Entity Type

Law Practice, Law Firm, Healthcare Industry, Government

Colors

Designer to choose colors to be used in the design.

Requirements
Nice to have
• **Please create a vertical design for the business card**

```html
<!DOCTYPE html>
<html lang="en">
<head>
<meta charset="utf-8">
<title>Maplecrest Disability – Letterhead</title>
<link href="https://fonts.googleapis.com/css2?family=Open+Sans:wght@400;700&display=swap" rel="stylesheet">
<style>
  :root {
    --backdrop: #d8dcdd;
    --paper: #ffffff;
    --brand-blue: #3559c9;
    --brand-orange: #f07a12;
    --band-orange: #ef7410;
    --band-yellow: #ffd000;
    --band-mist: #eef4f6;
    --band-cyan: #19d2f3;
    --ink-grey: #555a60;
    --rule-grey: #c9ccd0;
  }
  * { margin: 0; padding: 0; box-sizing: border-box; }
  html, body { width: 1200px; height: 784px; overflow: hidden; }
  body {
    background: var(--backdrop);
    display: flex; align-items: center; justify-content: center;
  }
  .letterhead {
    position: relative;
    width: 572px; height: 740px;
    background: var(--paper);
    box-shadow: 0 6px 18px rgba(0,0,0,.12);
    overflow: hidden;
  }
  .side-band {
    position: absolute; left: 0; top: 0;
    width: 44px; height: 100%;
  }
  .brand-tab {
    position: absolute; left: 30px; top: 26px;
    width: 300px; height: 74px;
    background: var(--paper);
    border-top-left-radius: 10px;
    padding: 20px 0 0 14px;
  }
  .brand-name {
    display: flex; align-items: center; gap: 8px;
    font-family: "Open Sans", sans-serif; font-weight: 700;
    font-size: 19px; letter-spacing: .2px;
    color: var(--brand-blue);
    white-space: nowrap;
  }
  .brand-dot {
    width: 10px; height: 10px; border-radius: 50%;
    background: var(--brand-orange); flex: none;
  }
  .contact {
    position: absolute; left: 388px; top: 128px;
    padding-left: 14px;
    border-left: 1px solid var(--rule-grey);
    font-family: "Open Sans", sans-serif; font-weight: 700;
    font-style: normal;
    font-size: 8.6px; line-height: 13px;
    color: var(--ink-grey);
  }
  .contact-row { display: flex; gap: 6px; align-items: flex-start; white-space: nowrap; }
  .contact-row svg { flex: none; margin-top: 2px; }
  .contact-address { color: var(--brand-orange); }
</style>
</head>
<body>
  <main class="letterhead">
    <svg class="side-band" viewBox="0 0 44 740" preserveAspectRatio="none" aria-hidden="true">
      <defs>
        <linearGradient id="bandGradient" x1="0" y1="0" x2="0" y2="1">
          <stop offset="0" stop-color="var(--band-orange)"/>
          <stop offset=".22" stop-color="#f79a0c"/>
          <stop offset=".38" stop-color="var(--band-yellow)"/>
          <stop offset=".55" stop-color="var(--band-mist)"/>
          <stop offset=".72" stop-color="#8fe3f5"/>
          <stop offset="1" stop-color="var(--band-cyan)"/>
        </linearGradient>
      </defs>
      <rect width="44" height="740" fill="url(#bandGradient)"/>
      <polygon points="0,60 44,20 44,120 0,170" fill="#fff" opacity=".10"/>
      <polygon points="0,230 44,180 44,260 0,320" fill="#fff" opacity=".14"/>
      <polygon points="0,420 44,360 44,470 0,520" fill="#fff" opacity=".18"/>
      <polygon points="0,600 44,540 44,640 0,700" fill="#fff" opacity=".12"/>
    </svg>

    <header class="brand-tab">
      <div class="brand-name"><span class="brand-dot"></span>Maplecrest Disability</div>
    </header>

    <address class="contact">
      <div class="contact-row contact-address">
        <svg width="8" height="8" viewBox="0 0 8 8"><circle cx="4" cy="4" r="4" fill="var(--brand-orange)"/><circle cx="4" cy="3.4" r="1.3" fill="#fff"/></svg>
        <span>0000 Example , Ste 240,<br>California, 90000, United States</span>
      </div>
      <div class="contact-row">
        <svg width="8" height="8" viewBox="0 0 8 8"><circle cx="4" cy="4" r="4" fill="var(--brand-orange)"/><path d="M2.6 2.2l1 1-.5.6a3 3 0 0 0 1.1 1.1l.6-.5 1 1-.6.7c-1.6-.3-2.9-1.6-3.2-3.2z" fill="#fff"/></svg>
        <span>(000) 000-0000</span>
      </div>
      <div class="contact-row">
        <svg width="8" height="8" viewBox="0 0 8 8"><circle cx="4" cy="4" r="4" fill="var(--brand-orange)"/><rect x="2.3" y="3" width="3.4" height="2.4" fill="#fff"/></svg>
        <span>(000) 000-0000</span>
      </div>
      <div class="contact-row">
        <svg width="8" height="8" viewBox="0 0 8 8"><circle cx="4" cy="4" r="4" fill="var(--brand-orange)"/><path d="M2.2 2.8h3.6v2.6H2.2z M2.2 2.8L4 4.2l1.8-1.4" fill="none" stroke="#fff" stroke-width=".6"/></svg>
        <span>info@maplecrestdisability.com</span>
      </div>
      <div class="contact-row">
        <svg width="8" height="8" viewBox="0 0 8 8"><circle cx="4" cy="4" r="4" fill="var(--brand-orange)"/><circle cx="4" cy="4" r="1.8" fill="none" stroke="#fff" stroke-width=".6"/></svg>
        <span>www.maplecrestdisability.com</span>
      </div>
    </address>
  </main>
</body>
</html>
```